Cool Website Design Gleam Shell Crew.

We need a new website, using our existing domain, with a similar function to https://www.marbeckfilm.com/ or https://www.tolvanfinishworks.com/ instagram gleam_shell.crew.
We can send google docs with pictures.
Logo attached

```html
<!DOCTYPE html>
<html lang="en">
<head>
<meta charset="utf-8">
<title>Gleam Shell Crew – Website Design</title>
<link href="https://fonts.googleapis.com/css2?family=Barlow:ital,wght@0,700;1,800&family=Roboto:wght@400;500;700&display=swap" rel="stylesheet">
<style>
:root{
  --ink:#000;
  --card:#0e0e14;
  --blue:#3c6ff0;
  --violet:#7a3fe6;
  --cyan:#159fe9;
  --white:#fff;
  --muted:#c9c9d4;
  --line:rgba(255,255,255,.55);
  --head:'Barlow',sans-serif;
  --body:'Roboto',sans-serif;
}
*{box-sizing:border-box;margin:0;padding:0}
html,body{width:806px;height:1200px;overflow:hidden;background:#fff}
.frame{position:relative;width:806px;height:1200px;overflow:hidden;background:#fff}
.stage{position:absolute;left:1px;top:0;width:1568px;height:2340px;transform:scale(.5128);transform-origin:0 0;background:#fff}
.page{position:absolute;top:53px;width:713px;height:2228px;background:var(--ink);color:var(--white);font-family:var(--body);overflow:hidden}
.page--a{left:50px}
.page--b{left:805px}
.abs{position:absolute}
.h{font-family:var(--head);font-style:italic;font-weight:800;text-transform:uppercase;letter-spacing:-.2px;white-space:nowrap}
.slashes{display:inline-flex;gap:3px;vertical-align:middle;margin:0 8px}
.slashes i{display:block;width:4px;height:18px;transform:skewX(-28deg);background:linear-gradient(var(--cyan),var(--violet))}
.btn{position:absolute;display:flex;align-items:center;justify-content:center;font-size:8px;font-weight:700;text-transform:uppercase;color:var(--white);height:25px;padding:0 11px;white-space:nowrap}
.btn--fill{background:linear-gradient(90deg,var(--violet),var(--blue))}
.btn--line{border:1px solid var(--white)}
.btn--white{background:var(--white);color:var(--blue)}
.btn::after{content:"›";margin-left:5px;font-size:10px}

/* header */
.brand{left:88px;top:12px;font-size:10px;font-weight:700;color:var(--violet);text-transform:uppercase;white-space:nowrap}
.brand-mark{left:88px;top:27px;width:76px;height:24px;background:linear-gradient(90deg,var(--violet),var(--blue));clip-path:polygon(18% 0,100% 0,82% 100%,0 100%)}
.call{left:398px;top:7px;width:128px;height:26px;border:1px solid var(--white);font-size:8px;font-weight:500;display:flex;align-items:center;justify-content:center;gap:5px;white-space:nowrap}
.quote{left:532px;top:7px;width:95px;height:26px;background:var(--blue);font-size:8px;font-weight:500;display:flex;align-items:center;justify-content:center;white-space:nowrap}
.navband{left:188px;top:40px;width:525px;height:22px;background:var(--blue);clip-path:polygon(22px 0,100% 0,100% 100%,0 100%)}
.nav{left:218px;top:40px;height:22px;display:flex;align-items:center;gap:25px;font-size:8px;font-weight:500;text-transform:uppercase;white-space:nowrap}
.nav .on{text-decoration:underline}

/* hero */
.hero{left:0;top:62px;width:713px;height:332px}
.page--a .hero{background:linear-gradient(90deg,#3b342b 0%,#6a5a3f 25%,#8f9296 48%,#c8c9cb 62%,#2a2d33 80%,#1a1c20 100%)}
.page--b .hero{background:linear-gradient(90deg,#24272c 0%,#34383e 35%,#6e5b4d 58%,#3c3f46 78%,#16181c 100%)}
.hero-shade{left:0;top:62px;width:420px;height:332px;background:linear-gradient(90deg,rgba(0,0,0,.55),rgba(0,0,0,0))}
.kicker{left:85px;top:117px;font-size:7.5px;font-weight:700;color:var(--cyan);text-transform:uppercase;white-space:nowrap}
.hero-title{left:86px;top:137px;font-size:31px;line-height:41px}
.hero-copy{left:85px;top:224px;width:260px;font-size:9.5px;line-height:17px}
.dots{left:342px;top:366px;display:flex;gap:3px}
.dots i{width:5px;height:5px;border-radius:50%;border:1px solid var(--white)}
.dots i.on{background:var(--white)}

/* about */
.about-mark{left:60px;top:458px;width:295px;height:116px;background:linear-gradient(90deg,var(--violet),var(--blue));clip-path:polygon(28% 0,100% 0,72% 100%,0 100%);display:flex;align-items:center;justify-content:center}
.about-mark span{font-size:18px;font-weight:700;color:var(--white);text-transform:uppercase;white-space:nowrap}
.sec-title{font-size:21px;display:flex;align-items:center}
.about-title{left:380px;top:437px}
.about-copy{left:380px;top:476px;width:252px;font-size:7.5px;line-height:14.3px;color:var(--muted)}

/* services */
.services{left:0;top:636px;width:713px;height:382px;background:linear-gradient(180deg,#0b0b10,#000)}
.services-title{left:0;top:674px;width:713px;justify-content:center}
.services-copy{left:85px;top:716px;width:543px;text-align:center;font-size:7.5px;line-height:14px;color:var(--muted)}
.cards{left:24px;top:762px;width:680px;height:166px}
.card{position:absolute;top:0;width:178px;height:166px;clip-path:polygon(12px 0,100% 0,calc(100% - 12px) 100%,0 100%)}
.card span{position:absolute;bottom:12px;left:0;width:100%;text-align:center;font-size:9.5px;font-weight:500;white-space:nowrap}
.card--1{left:0;background:linear-gradient(160deg,#4a4d55,#272930 60%,#6b4a3a)}
.card--2{left:168px;background:linear-gradient(160deg,#3a3a36,#1f1f22 55%,#5a3a2e)}
.card--3{left:336px;background:linear-gradient(160deg,#c99b4a,#4a63a8 55%,#2a3f86)}
.card--4{left:504px;background:linear-gradient(160deg,#50545c,#272a30 55%,#a3242a)}
.arrow{position:absolute;top:834px;width:20px;height:20px;border-radius:50%;background:var(--white);color:#000;font-size:11px;display:flex;align-items:center;justify-content:center}

/* cta */
.cta{left:0;top:1018px;width:713px;height:186px;background:linear-gradient(90deg,var(--cyan),var(--blue) 50%,var(--violet))}
.cta-title{left:0;top:1044px;width:713px;text-align:center;font-size:21px;line-height:33px}
.cta-sub{left:0;top:1117px;width:713px;text-align:center;font-size:9.5px}

/* gallery */
.gallery-title{left:87px;top:1245px}
.gallery-copy{left:85px;top:1280px;width:195px;font-size:7.5px;line-height:14.3px;color:var(--muted)}
.tile{position:absolute;clip-path:polygon(8px 0,100% 0,calc(100% - 8px) 100%,0 100%)}

/* reviews */
.reviews-title{left:0;top:1450px;width:713px;justify-content:center}
.review{position:absolute;top:1500px;width:178px;height:130px;border:1px solid #2a2a33;background:var(--card);padding:10px 12px;transform:skewX(-2deg)}
.review>*{transform:skewX(2deg)}
.who{display:flex;gap:8px;align-items:center}
.avatar{width:26px;height:26px;border-radius:50%;background:linear-gradient(#c9b8a6,#7a6b5e)}
.name{font-size:9px;font-weight:500}
.date{font-size:6px;color:#9a9aa6;margin-top:2px}
.stars{color:#f5c518;font-size:10px;letter-spacing:1px;margin:7px 0 5px}
.quote-text{font-size:6.8px;line-height:12px;color:var(--muted)}
.chev{position:absolute;top:1558px;font-size:14px}

/* contact */
.contact{left:0;top:1668px;width:713px;height:338px;background:linear-gradient(90deg,#1890ea,var(--blue) 50%,#6a47dc)}
.contact-title{left:0;top:1702px;width:713px;justify-content:center}
.contact-sub{left:0;top:1747px;width:713px;text-align:center;font-size:9.5px}
.field{position:absolute;height:27px;border:1px solid var(--line);font-size:7px;padding:0 0 0 18px;display:flex;align-items:center;color:#e8ecff}
.field--area{align-items:flex-start;padding-top:10px}

/* footer */
.foot-brand{left:92px;top:2058px;font-size:16px;font-weight:700;color:var(--violet);text-transform:uppercase;white-space:nowrap}
.foot-mark{left:85px;top:2085px;width:124px;height:38px;background:linear-gradient(90deg,var(--violet),var(--blue));clip-path:polygon(20% 0,100% 0,80% 100%,0 100%)}
.col h4{font-size:8.5px;font-weight:500;text-transform:uppercase;margin-bottom:5px}
.col li{list-style:none;font-size:7.5px;line-height:12.3px;color:var(--muted)}
.col li::before{content:"»";margin-right:8px}
.info{display:flex;gap:7px;font-size:7.5px;line-height:11px;color:var(--muted);margin-bottom:10px;align-items:flex-start}
.info b{flex:none;width:12px;height:12px;border-radius:50%;background:var(--blue);color:var(--white);font-size:7px;display:flex;align-items:center;justify-content:center;font-weight:400}
.rule{left:85px;top:2164px;width:543px;height:1px;background:#222}
.copy{left:0;top:2174px;width:713px;text-align:center;font-size:7px;color:var(--muted)}
.social{left:327px;top:2194px;display:flex;gap:6px}
.social i{width:16px;height:16px;border-radius:50%;border:1px solid var(--white)}
.social i.on{background:var(--blue);border-color:var(--blue)}
</style>
</head>
<body>
<div class="frame">
<div class="stage">

<section class="page page--a">
  <div class="abs brand">Gleam Shell Crew</div>
  <div class="abs brand-mark"></div>
  <div class="abs call">&#9742; CALL US 1-888-888-8888</div>
  <div class="abs quote">GET A FREE QUOTE</div>
  <div class="abs navband"></div>
  <nav class="abs nav"><span class="on">Home</span><span>About Us</span><span>Services</span><span>Promotions</span><span>Gallery</span><span>FAQs</span><span>Contact</span></nav>

  <div class="abs hero" role="img" aria-label="Installer applying clear film to a dark SUV in a workshop"></div>
  <div class="abs hero-shade"></div>
  <div class="abs kicker">Welcome to Gleam Shell Crew</div>
  <h1 class="abs h hero-title">/// Stand out every<br>where you go.</h1>
  <p class="abs hero-copy">Premium vehicle wraps, fleet graphics, and custom designs that make you stand out on the road.</p>
  <a class="btn btn--fill" style="left:85px;top:275px">Protect your vehicle</a>
  <a class="btn btn--line" style="left:230px;top:275px">Change your colour</a>
  <div class="abs dots"><i></i><i class="on"></i><i></i><i></i></div>

  <div class="abs about-mark"><span>Gleam Shell Crew</span></div>
  <h2 class="abs h sec-title about-title">About us<span class="slashes"><i></i><i></i><i></i></span></h2>
  <p class="abs about-copy">Lorem ipsum dolor sit amet, consectetur adipiscing elit, sed do eiusmod tempor incididunt ut labore et dolore magna aliqua. Ut enim ad minim veniam, quis nostrud exercitation ullamco laboris nisi ut aliquip ex ea commodo consequat, duis aute irure dolor in reprehenderit in voluptate velit esse cillum dolore eu fugiat nulla pariatur.</p>
  <a class="btn btn--fill" style="left:380px;top:564px">Read more</a>

  <div class="abs services"></div>
  <h2 class="abs h sec-title services-title"><span class="slashes"><i></i><i></i><i></i></span>Our services<span class="slashes"><i></i><i></i><i></i></span></h2>
  <p class="abs services-copy">Lorem ipsum dolor sit amet, consectetur adipiscing elit, sed do eiusmod tempor incididunt ut labore et dolore magna aliqua. Ut enim ad minim veniam, quis nostrud exercitation ullamco laboris nisi ut aliquip ex ea commodo consequat.</p>
  <div class="abs cards">
    <div class="card card--1" role="img" aria-label="Technician fitting paint protection film"><span>Paint Protection Film</span></div>
    <div class="card card--2" role="img" aria-label="Technician applying vinyl wrap"><span>Vinyl Wraps</span></div>
    <div class="card card--3" role="img" aria-label="Technician tinting a car window"><span>Window Tinting</span></div>
    <div class="card card--4" role="img" aria-label="Technician coating a red car"><span>Ceramic Coating</span></div>
  </div>
  <div class="arrow" style="left:15px">‹</div>
  <div class="arrow" style="left:682px">›</div>
  <a class="btn btn--fill" style="left:316px;top:952px">Learn more</a>

  <div class="abs cta"></div>
  <h2 class="abs h cta-title">Boost visibility, build trust, stand out<br>everywhere you go</h2>
  <p class="abs cta-sub">Get A Custom Wrap That Turns Heads and Drives Results.</p>
  <a class="btn btn--line" style="left:304px;top:1146px">Get a free quote</a>

  <h2 class="abs h sec-title gallery-title">Wrap gallery<span class="slashes"><i></i><i></i><i></i></span></h2>
  <p class="abs gallery-copy">Lorem ipsum dolor sit amet, consectetur adipiscing elit, sed do eiusmod tempor incididunt ut labore et dolore magna aliqua. Ut enim ad minim veniam, quis nostrud exercitation ullamco laboris</p>
  <a class="btn btn--fill" style="left:85px;top:1352px">View more</a>
  <div class="tile" style="left:300px;top:1204px;width:150px;height:104px;background:linear-gradient(#d8322e,#8a1b1a)" role="img" aria-label="Red hatchback with black stripe"></div>
  <div class="tile" style="left:450px;top:1204px;width:150px;height:140px;background:linear-gradient(#8f989c,#5c6266)" role="img" aria-label="Silver coupe with decal wrap"></div>
  <div class="tile" style="left:600px;top:1204px;width:113px;height:70px;background:linear-gradient(#d8cdb6,#8b8270)" role="img" aria-label="Beige sports car"></div>
  <div class="tile" style="left:290px;top:1310px;width:150px;height:106px;background:linear-gradient(#2f4fa0,#1a2a5a)" role="img" aria-label="Blue lettered wrap panel"></div>
  <div class="tile" style="left:440px;top:1346px;width:150px;height:70px;background:linear-gradient(#7c7b78,#3a3a3a)" role="img" aria-label="Grey car hood"></div>
  <div class="tile" style="left:592px;top:1276px;width:121px;height:140px;background:linear-gradient(#d9d9dc,#b2252c)" role="img" aria-label="White car with red stripes"></div>

  <h2 class="abs h sec-title reviews-title"><span class="slashes"><i></i><i></i><i></i></span>What customers say about us<span class="slashes"><i></i><i></i><i></i></span></h2>
  <span class="chev" style="left:60px">‹</span>
  <div class="review" style="left:80px"><div class="who"><div class="avatar" role="img" aria-label="Customer portrait"></div><div><div class="name">Iver Lund</div><div class="date">February 4, 2024</div></div></div><div class="stars">★★★★★</div><p class="quote-text">Lorem ipsum dolor sit amet, consectetur adipiscing elit, sed do eiusmod tempor incididunt ut labore et dolore magna aliqua. Ut enim ad minim veniam,</p></div>
  <div class="review" style="left:265px"><div class="who"><div class="avatar" role="img" aria-label="Customer portrait"></div><div><div class="name">Mara Quell</div><div class="date">February 4, 2024</div></div></div><div class="stars">★★★★★</div><p class="quote-text">Lorem ipsum dolor sit amet, consectetur adipiscing elit, sed do eiusmod tempor incididunt ut labore et dolore magna aliqua. Ut enim ad minim veniam,</p></div>
  <div class="review" style="left:450px"><div class="who"><div class="avatar" role="img" aria-label="Customer portrait"></div><div><div class="name">Tobin Ash</div><div class="date">February 4, 2024</div></div></div><div class="stars">★★★★★</div><p class="quote-text">Lorem ipsum dolor sit amet, consectetur adipiscing elit, sed do eiusmod tempor incididunt ut labore et dolore magna aliqua. Ut enim ad minim veniam,</p></div>
  <span class="chev" style="left:644px">›</span>

  <div class="abs contact"></div>
  <h2 class="abs h sec-title contact-title"><span class="slashes"><i></i><i></i><i></i></span>Contact us<span class="slashes"><i></i><i></i><i></i></span></h2>
  <p class="abs contact-sub">Send Us A Message To Schedule A Call Us 1-888-888-8888 or Message Below To Book!</p>
  <div class="field" style="left:107px;top:1776px;width:243px">First Name</div>
  <div class="field" style="left:363px;top:1776px;width:243px">Last Name</div>
  <div class="field" style="left:107px;top:1817px;width:243px">Email Address</div>
  <div class="field" style="left:363px;top:1817px;width:243px">Phone Number</div>
  <div class="field field--area" style="left:107px;top:1858px;width:499px;height:62px">Write Your Message Here</div>
  <a class="btn btn--white" style="left:316px;top:1938px">Submit now</a>

  <div class="abs foot-brand">Gleam Shell Crew</div>
  <div class="abs foot-mark"></div>
  <div class="abs col" style="left:255px;top:2044px"><h4>Quick Links</h4><ul><li>Home</li><li>About Us</li><li>Services</li><li>Promotions</li><li>Gallery</li><li>Faqs</li><li>Contact</li></ul></div>
  <div class="abs col" style="left:363px;top:2044px"><h4>Other Links</h4><ul><li>Financing</li><li>Gallery</li><li>Blog</li><li>Jobs</li><li>Warranty</li></ul></div>
  <div class="abs col" style="left:482px;top:2044px;width:160px"><h4>Contact Us</h4>
    <div class="info"><b>&#9742;</b>+1-888-888-8888</div>
    <div class="info"><b>@</b>info@gleamshellcrew.com</div>
    <div class="info"><b>&#9679;</b>10 Duis aute irure dolor in reprehen derit voluptate 5263,USA</div>
    <div class="info"><b>&#9719;</b>Mon To Sat: 8.00 AM To 9 PM</div>
  </div>
  <div class="abs rule"></div>
  <div class="abs copy">© 2025 Gleam Shell Crew &nbsp;|&nbsp; All Rights Reserved</div>
  <div class="abs social"><i></i><i class="on"></i><i></i></div>
</section>

<section class="page page--b">
  <div class="abs brand">Gleam Shell Crew</div>
  <div class="abs brand-mark"></div>
  <div class="abs call">&#9742; CALL US 1-888-888-8888</div>
  <div class="abs quote">GET A FREE QUOTE</div>
  <div class="abs navband"></div>
  <nav class="abs nav"><span class="on">Home</span><span>About Us</span><span>Services</span><span>Promotions</span><span>Gallery</span><span>FAQs</span><span>Contact</span></nav>

  <div class="abs hero" role="img" aria-label="Installer smoothing wrap film across a car bonnet"></div>
  <div class="abs hero-shade"></div>
  <div class="abs kicker">Welcome to Gleam Shell Crew</div>
  <h1 class="abs h hero-title">/// Stand out every<br>where you go.</h1>
  <p class="abs hero-copy">Premium vehicle wraps, fleet graphics, and custom designs that make you stand out on the road.</p>
  <a class="btn btn--fill" style="left:85px;top:275px">Protect your vehicle</a>
  <a class="btn btn--line" style="left:230px;top:275px">Change your colour</a>
  <div class="abs dots"><i></i><i class="on"></i><i></i><i></i></div>

  <div class="abs about-mark"><span>Gleam Shell Crew</span></div>
  <h2 class="abs h sec-title about-title">About us<span class="slashes"><i></i><i></i><i></i></span></h2>
  <p class="abs about-copy">Lorem ipsum dolor sit amet, consectetur adipiscing elit, sed do eiusmod tempor incididunt ut labore et dolore magna aliqua. Ut enim ad minim veniam, quis nostrud exercitation ullamco laboris nisi ut aliquip ex ea commodo consequat, duis aute irure dolor in reprehenderit in voluptate velit esse cillum dolore eu fugiat nulla pariatur.</p>
  <a class="btn btn--fill" style="left:380px;top:564px">Read more</a>

  <div class="abs services"></div>
  <h2 class="abs h sec-title services-title"><span class="slashes"><i></i><i></i><i></i></span>Our services<span class="slashes"><i></i><i></i><i></i></span></h2>
  <p class="abs services-copy">Lorem ipsum dolor sit amet, consectetur adipiscing elit, sed do eiusmod tempor incididunt ut labore et dolore magna aliqua. Ut enim ad minim veniam, quis nostrud exercitation ullamco laboris nisi ut aliquip ex ea commodo consequat.</p>
  <div class="abs cards">
    <div class="card card--1" role="img" aria-label="Technician fitting paint protection film"><span>Paint Protection Film</span></div>
    <div class="card card--2" role="img" aria-label="Technician applying vinyl wrap"><span>Vinyl Wraps</span></div>
    <div class="card card--3" role="img" aria-label="Technician tinting a car window"><span>Window Tinting</span></div>
    <div class="card card--4" role="img" aria-label="Technician coating a red car"><span>Ceramic Coating</span></div>
  </div>
  <div class="arrow" style="left:15px">‹</div>
  <div class="arrow" style="left:682px">›</div>
  <a class="btn btn--fill" style="left:316px;top:952px">Learn more</a>

  <div class="abs cta"></div>
  <h2 class="abs h cta-title">Boost visibility, build trust, stand out<br>everywhere you go</h2>
  <p class="abs cta-sub">Get A Custom Wrap That Turns Heads and Drives Results.</p>
  <a class="btn btn--line" style="left:304px;top:1146px">Get a free quote</a>

  <h2 class="abs h sec-title gallery-title">Wrap gallery<span class="slashes"><i></i><i></i><i></i></span></h2>
  <p class="abs gallery-copy">Lorem ipsum dolor sit amet, consectetur adipiscing elit, sed do eiusmod tempor incididunt ut labore et dolore magna aliqua. Ut enim ad minim veniam, quis nostrud exercitation ullamco laboris</p>
  <a class="btn btn--fill" style="left:85px;top:1352px">View more</a>
  <div class="tile" style="left:300px;top:1204px;width:150px;height:104px;background:linear-gradient(#d8322e,#8a1b1a)" role="img" aria-label="Red hatchback with black stripe"></div>
  <div class="tile" style="left:450px;top:1204px;width:150px;height:140px;background:linear-gradient(#8f989c,#5c6266)" role="img" aria-label="Silver coupe with decal wrap"></div>
  <div class="tile" style="left:600px;top:1204px;width:113px;height:70px;background:linear-gradient(#d8cdb6,#8b8270)" role="img" aria-label="Beige sports car"></div>
  <div class="tile" style="left:290px;top:1310px;width:150px;height:106px;background:linear-gradient(#2f4fa0,#1a2a5a)" role="img" aria-label="Blue lettered wrap panel"></div>
  <div class="tile" style="left:440px;top:1346px;width:150px;height:70px;background:linear-gradient(#7c7b78,#3a3a3a)" role="img" aria-label="Grey car hood"></div>
  <div class="tile" style="left:592px;top:1276px;width:121px;height:140px;background:linear-gradient(#d9d9dc,#b2252c)" role="img" aria-label="White car with red stripes"></div>

  <h2 class="abs h sec-title reviews-title"><span class="slashes"><i></i><i></i><i></i></span>What customers say about us<span class="slashes"><i></i><i></i><i></i></span></h2>
  <span class="chev" style="left:60px">‹</span>
  <div class="review" style="left:80px"><div class="who"><div class="avatar" role="img" aria-label="Customer portrait"></div><div><div class="name">Iver Lund</div><div class="date">February 4, 2024</div></div></div><div class="stars">★★★★★</div><p class="quote-text">Lorem ipsum dolor sit amet, consectetur adipiscing elit, sed do eiusmod tempor incididunt ut labore et dolore magna aliqua. Ut enim ad minim veniam,</p></div>
  <div class="review" style="left:265px"><div class="who"><div class="avatar" role="img" aria-label="Customer portrait"></div><div><div class="name">Mara Quell</div><div class="date">February 4, 2024</div></div></div><div class="stars">★★★★★</div><p class="quote-text">Lorem ipsum dolor sit amet, consectetur adipiscing elit, sed do eiusmod tempor incididunt ut labore et dolore magna aliqua. Ut enim ad minim veniam,</p></div>
  <div class="review" style="left:450px"><div class="who"><div class="avatar" role="img" aria-label="Customer portrait"></div><div><div class="name">Tobin Ash</div><div class="date">February 4, 2024</div></div></div><div class="stars">★★★★★</div><p class="quote-text">Lorem ipsum dolor sit amet, consectetur adipiscing elit, sed do eiusmod tempor incididunt ut labore et dolore magna aliqua. Ut enim ad minim veniam,</p></div>
  <span class="chev" style="left:644px">›</span>

  <div class="abs contact"></div>
  <h2 class="abs h sec-title contact-title"><span class="slashes"><i></i><i></i><i></i></span>Contact us<span class="slashes"><i></i><i></i><i></i></span></h2>
  <p class="abs contact-sub">Send Us A Message To Schedule A Call Us 1-888-888-8888 or Message Below To Book!</p>
  <div class="field" style="left:107px;top:1776px;width:243px">First Name</div>
  <div class="field" style="left:363px;top:1776px;width:243px">Last Name</div>
  <div class="field" style="left:107px;top:1817px;width:243px">Email Address</div>
  <div class="field" style="left:363px;top:1817px;width:243px">Phone Number</div>
  <div class="field field--area" style="left:107px;top:1858px;width:499px;height:62px">Write Your Message Here</div>
  <a class="btn btn--white" style="left:316px;top:1938px">Submit now</a>

  <div class="abs foot-brand">Gleam Shell Crew</div>
  <div class="abs foot-mark"></div>
  <div class="abs col" style="left:255px;top:2044px"><h4>Quick Links</h4><ul><li>Home</li><li>About Us</li><li>Services</li><li>Promotions</li><li>Gallery</li><li>Faqs</li><li>Contact</li></ul></div>
  <div class="abs col" style="left:363px;top:2044px"><h4>Other Links</h4><ul><li>Financing</li><li>Gallery</li><li>Blog</li><li>Jobs</li><li>Warranty</li></ul></div>
  <div class="abs col" style="left:482px;top:2044px;width:160px"><h4>Contact Us</h4>
    <div class="info"><b>&#9742;</b>+1-888-888-8888</div>
    <div class="info"><b>@</b>info@gleamshellcrew.com</div>
    <div class="info"><b>&#9679;</b>10 Duis aute irure dolor in reprehen derit voluptate 5263,USA</div>
    <div class="info"><b>&#9719;</b>Mon To Sat: 8.00 AM To 9 PM</div>
  </div>
  <div class="abs rule"></div>
  <div class="abs copy">© 2025 Gleam Shell Crew &nbsp;|&nbsp; All Rights Reserved</div>
  <div class="abs social"><i></i><i class="on"></i><i></i></div>
</section>

</div>
</div>
</body>
</html>
```